Business Card Design

We have recently seen two business cards that caught our attention and think the designs would work for us. We are an accounting firm that serves small businesses in a variety of industries. Attached are the two business card that inspired us along with very rough layouts. We would like to see a professional layout using our company information.

Industry/Entity Type

Accounting

Contact Information for Business Card

Company Name - Marlowe Thistle
Address - 4182 Orlanby Lane, Suite 610, Houston, TX 77093
713-555-0187 - Main
281-555-0342 - Fax

Team Member Names, emails and phone numbers (see attachment)

```html
<!DOCTYPE html>
<html lang="en">
<head>
<meta charset="utf-8">
<title>Marlowe Thistle – Business Card</title>
<link href="https://fonts.googleapis.com/css2?family=Lato:wght@400;700;900&display=swap" rel="stylesheet">
<style>
  :root {
    --backdrop: #e6e4e1;
    --card: #ffffff;
    --band-grey: #d6d6d6;
    --ink: #111111;
    --ink-soft: #2b2b2b;
    --title-grey: #b5b5b5;
    --accent-grey: #9a9a9a;
    --band-black: #050505;
    --on-black: #ffffff;
  }
  * { box-sizing: border-box; margin: 0; padding: 0; }
  html, body {
    width: 1200px; height: 900px; overflow: hidden;
    background: var(--backdrop);
    font-family: "Lato", Arial, sans-serif;
    color: var(--ink);
  }
  .stage {
    width: 1200px; height: 900px;
    display: flex; align-items: center; justify-content: center;
  }
  .business-card {
    width: 470px; height: 820px;
    background: var(--card);
    display: flex; flex-direction: column;
    box-shadow: 0 6px 24px rgba(0,0,0,0.18);
  }
  .holder-band {
    margin-top: 22px;
    height: 56px;
    background: var(--band-grey);
    display: flex; align-items: center; justify-content: center;
  }
  .holder-name {
    font-weight: 900; font-size: 30px; letter-spacing: 0.5px;
    color: var(--ink-soft); text-transform: uppercase;
  }
  .holder-title {
    text-align: center; margin-top: 6px;
    font-size: 25px; letter-spacing: 1.5px;
    color: var(--title-grey); text-transform: uppercase;
  }
  .holder-contacts {
    margin-top: 8px;
    display: flex; flex-direction: column; align-items: center; gap: 4px;
    font-weight: 700; font-size: 23px;
  }
  .contact-row { display: flex; align-items: center; gap: 16px; }
  .contact-item { display: flex; align-items: center; gap: 6px; }
  .icon { width: 20px; height: 20px; flex: none; }
  .mark-area {
    flex: 1;
    display: flex; align-items: center; justify-content: center; gap: 14px;
  }
  .mark-square { width: 22px; height: 22px; background: var(--accent-grey); }
  .mark-name {
    font-weight: 900; font-size: 40px; color: var(--ink);
  }
  .company-band {
    height: 78px; background: var(--band-black);
    display: flex; align-items: center; justify-content: center;
  }
  .company-name {
    color: var(--on-black); font-weight: 900; font-size: 38px;
    letter-spacing: 0.5px; text-transform: uppercase;
  }
  .grey-strip { height: 28px; background: var(--band-grey); }
  .office-row {
    height: 62px;
    display: flex; align-items: center; justify-content: center; gap: 8px;
    font-weight: 700; font-size: 16.5px;
  }
  .lines-row {
    height: 66px;
    display: flex; align-items: center; justify-content: center; gap: 34px;
    font-weight: 700; font-size: 25px;
  }
  .lines-row .contact-item { gap: 10px; }
  .bottom-strip { height: 40px; background: var(--band-grey); margin-bottom: 22px; }
</style>
</head>
<body>
<main class="stage">
  <article class="business-card">
    <header class="holder-band">
      <h1 class="holder-name">Delphine Ardmore</h1>
    </header>
    <p class="holder-title">Account Manager</p>

    <section class="holder-contacts">
      <div class="contact-row">
        <span class="contact-item">
          <svg class="icon" viewBox="0 0 20 20" aria-hidden="true"><rect x="5" y="1.5" width="10" height="17" rx="1.5" fill="none" stroke="currentColor" stroke-width="1.6"/><circle cx="10" cy="15.5" r="1" fill="currentColor"/></svg>
          832-555-0129
        </span>
        <span class="contact-item">
          <svg class="icon" viewBox="0 0 20 20" aria-hidden="true"><path d="M2 7c0-3 3-4 8-4s8 1 8 4l-3 1-1-2H6L5 8z" fill="currentColor"/><path d="M5 9h10l2 8H3z" fill="currentColor"/><circle cx="10" cy="13" r="2" fill="#fff"/></svg>
          713-555-0187
        </span>
      </div>
      <span class="contact-item">
        <svg class="icon" viewBox="0 0 20 20" aria-hidden="true"><rect x="1.5" y="4" width="17" height="12" fill="currentColor"/><path d="M2 5l8 6 8-6" fill="none" stroke="#fff" stroke-width="1.4"/></svg>
        dardmore@marlowethistle.com
      </span>
    </section>

    <section class="mark-area">
      <span class="mark-square" aria-hidden="true"></span>
      <span class="mark-name">Marlowe Thistle</span>
    </section>

    <div class="company-band">
      <h2 class="company-name">Marlowe Thistle</h2>
    </div>
    <div class="grey-strip"></div>

    <div class="office-row">
      <svg class="icon" viewBox="0 0 20 20" aria-hidden="true"><path d="M10 2L1 10h3v8h4v-5h4v5h4v-8h3z" fill="currentColor"/></svg>
      <span>4182 Orlanby Lane, Suite 610, Houston, TX 77093</span>
    </div>
    <div class="grey-strip"></div>

    <div class="lines-row">
      <span class="contact-item">
        <svg class="icon" viewBox="0 0 20 20" aria-hidden="true"><path d="M2 7c0-3 3-4 8-4s8 1 8 4l-3 1-1-2H6L5 8z" fill="currentColor"/><path d="M5 9h10l2 8H3z" fill="currentColor"/><circle cx="10" cy="13" r="2" fill="#fff"/></svg>
        713-555-0187
      </span>
      <span class="contact-item">
        <svg class="icon" viewBox="0 0 20 20" aria-hidden="true"><rect x="5" y="2" width="10" height="5" fill="currentColor"/><rect x="1.5" y="7" width="17" height="7" rx="1" fill="currentColor"/><rect x="5" y="12" width="10" height="6" fill="#fff" stroke="currentColor" stroke-width="1.4"/></svg>
        281-555-0342
      </span>
    </div>
    <div class="bottom-strip"></div>
  </article>
</main>
</body>
</html>
```